New Technology Company is Launching New Products with a New Website

We want to create a 4-page website in WordPress compatible files to launch our site on HostMeadow. The attached files provide our ideas for Products, Services and About Us pages. We believe the content in those files is about right but the actual design is up to the artist that wants to accept this challenge. Additionally we need a fantastic Home page but we have no idea what that looks like. It obviously needs to lead to the other 3 pages but more importantly it needs to capture the interest of our current and future customers.

Details:
1. Please start off using the text descriptions in the example files. If shorter, longer, different descriptions are needed, just let us know.

2. Please feel free to suggest any photos you can find from free or reasonable stock photo services. Picvault and others like them are reasonable. If you find a perfect image, please send us a link and we will buy a license if its affordable. I have paid ~US$10 per image in the past.

3. I have also uploaded our stationery and logo files. We would like the website design to be consistent with the logo and stationery designs. The stationery designs are all in one file.

We have two logos, and would like to see both of them used on the website. One logo shows the letters KRTV in an outlined shield that is read and blue. That logo is used in the stationery and in our draft website design as a header. The other logo shows flames bouncing off a round shield. Perhaps this logo could be used at the bottom of each page on the website, or some other place where it would be fun and creative without diminishing the seriousness of our underlying science and engineering.

4. We are looking for an artist to have some fun with this and propose something creative. We have lots of boring ideas ourselves so we need YOU to do something else! Thank you so much for considering this challenge!

Target Market(s)

People interested in new, high performance fabrics, including consumers, store owners, garment designers and companies like Wolverock or The Ridge Pelt

Coding

Coded - Design and coding required

Font styles to use
Sans Serif

Colors
f04a51
3277b5

Requirements
Must have
• something unforgetable

```html
<!DOCTYPE html>
<html lang="en">
<head>
<meta charset="utf-8">
<title>KRTV – High Temperature Insulations</title>
<link rel="stylesheet" href="https://fonts.googleapis.com/css2?family=Roboto:wght@400;500;700&family=Open+Sans:wght@400&display=swap">
<style>
  :root {
    --brand-blue: #1460ad;
    --nav-band: rgba(16, 44, 84, 0.78);
    --white: #ffffff;
    --ink: #222831;
    --muted: #555a60;
    --rule: #dcdfe3;
    --social-ring: #6d7683;
    --social-ink: #16457e;
    --accent-red: #f04a51;
    --accent-blue: #3277b5;
    --fire-deep: #1e0702;
    --fire-ember: #6e1d05;
    --fire-mid: #c4470c;
    --fire-hot: #f7a21f;
    --fire-glow: #ffd04a;
  }
  * { margin: 0; padding: 0; box-sizing: border-box; }
  html, body { width: 1200px; height: 1066px; overflow: hidden; background: var(--white); }
  body { position: relative; font-family: 'Roboto', sans-serif; }

  .hero { position: absolute; left: 0; top: 0; width: 1200px; height: 705px; overflow: hidden; background: var(--fire-deep); }
  .hero-photo {
    position: absolute; inset: 0;
    background:
      radial-gradient(ellipse 170px 330px at 620px 470px, rgba(120,78,40,0.95) 0%, rgba(150,88,36,0.6) 55%, rgba(150,88,36,0) 100%),
      radial-gradient(ellipse 130px 90px at 90px 560px, var(--fire-glow) 0%, rgba(247,162,31,0) 100%),
      radial-gradient(ellipse 160px 110px at 300px 520px, var(--fire-glow) 0%, rgba(247,162,31,0) 100%),
      radial-gradient(ellipse 150px 120px at 960px 560px, var(--fire-glow) 0%, rgba(247,162,31,0) 100%),
      radial-gradient(ellipse 120px 90px at 1130px 470px, var(--fire-glow) 0%, rgba(247,162,31,0) 100%),
      radial-gradient(ellipse 90px 140px at 200px 300px, rgba(255,190,60,0.8) 0%, rgba(247,162,31,0) 100%),
      radial-gradient(ellipse 110px 160px at 1040px 300px, rgba(255,190,60,0.8) 0%, rgba(247,162,31,0) 100%),
      radial-gradient(ellipse 360px 420px at 190px 470px, var(--fire-hot) 0%, var(--fire-mid) 45%, rgba(196,71,12,0) 90%),
      radial-gradient(ellipse 360px 440px at 1020px 460px, var(--fire-hot) 0%, var(--fire-mid) 45%, rgba(196,71,12,0) 90%),
      linear-gradient(180deg, #4a1605 0%, var(--fire-ember) 35%, #8c2c08 60%, var(--fire-deep) 100%);
  }
  .hero-shade {
    position: absolute; inset: 0;
    background:
      radial-gradient(ellipse 760px 520px at 600px 400px, rgba(0,0,0,0) 55%, rgba(20,5,0,0.55) 100%),
      linear-gradient(180deg, rgba(0,0,0,0) 70%, rgba(20,5,0,0.45) 100%);
  }
  .header-wave { position: absolute; left: 0; top: 0; }
  .brand-mark {
    position: absolute; left: 116px; top: 58px;
    font-weight: 700; font-size: 54px; color: var(--white); letter-spacing: 1px;
  }
  .company-contact { position: absolute; left: 817px; top: 13px; color: var(--white); font-size: 15px; line-height: 22.4px; font-style: normal; }
  .contact-line { display: flex; align-items: flex-start; gap: 5px; }
  .contact-line svg { flex: none; margin-top: 3px; }
  .main-nav { position: absolute; left: 677px; top: 150px; display: flex; gap: 34px; }
  .main-nav a { color: var(--white); text-decoration: none; font-weight: 500; font-size: 15.5px; }
  .hero-title {
    position: absolute; left: 0; width: 1218px; top: 314px; text-align: center;
    color: var(--white); font-weight: 700; font-size: 47px; line-height: 46px;
  }
  .slider-controls { position: absolute; left: 558px; top: 668px; display: flex; align-items: center; gap: 4px; }
  .slider-arrow { width: 20px; height: 20px; border-radius: 50%; background: var(--white); display: flex; align-items: center; justify-content: center; }
  .slider-dot { width: 10px; height: 10px; border-radius: 50%; background: rgba(255,255,255,0.35); }
  .slider-dot.is-active { background: var(--white); }
  .slider-dots { display: flex; gap: 4px; margin: 0 4px; }

  .footer-brand { position: absolute; left: 125px; top: 820px; display: flex; align-items: center; gap: 12px; }
  .footer-brand .brand-dot { width: 28px; height: 28px; border-radius: 50%; background: var(--accent-blue); }
  .footer-brand span { font-weight: 700; font-size: 46px; color: var(--brand-blue); }

  .footer-col { position: absolute; top: 761px; height: 176px; border-left: 1px solid var(--rule); }
  .footer-col h3 { position: absolute; top: 3px; font-weight: 500; font-size: 18px; color: var(--ink); white-space: nowrap; }
  .footer-col ul { position: absolute; top: 45px; list-style: none; }
  .footer-col li { font-family: 'Open Sans', sans-serif; font-size: 12px; color: var(--muted); white-space: nowrap; }
  .col-info { left: 393px; } .col-info h3, .col-info ul { left: 51px; } .col-info li { height: 26.4px; }
  .col-help { left: 595px; } .col-help h3, .col-help ul { left: 51px; } .col-help li { height: 28.9px; }
  .col-account { left: 841px; } .col-account h3, .col-account ul { left: 54px; } .col-account li { height: 28.9px; }

  .footer-rule { position: absolute; left: 10px; top: 980px; width: 1153px; height: 1px; background: var(--rule); }
  .copyright { position: absolute; left: 104px; top: 1015px; font-family: 'Open Sans', sans-serif; font-size: 12px; color: var(--muted); }
  .social-links { position: absolute; left: 902px; top: 1006px; display: flex; gap: 6px; }
  .social-links a { width: 38px; height: 38px; border-radius: 50%; border: 1px solid var(--social-ring); display: flex; align-items: center; justify-content: center; }
</style>
</head>
<body>
  <section class="hero">
    <div class="hero-photo" role="img" aria-label="Firefighter in protective gear walking into a wall of flames"></div>
    <div class="hero-shade"></div>
    <svg class="header-wave" width="1200" height="182" viewBox="0 0 1200 182" aria-hidden="true">
      <path d="M396 0 C440 40 470 95 540 125 C560 134 575 139 600 139 L1200 139 L1200 0 Z" fill="var(--brand-blue)"/>
      <path d="M578 139 L1200 139 L1200 182 L590 182 C585 165 580 150 578 139 Z" fill="var(--nav-band)"/>
    </svg>
    <div class="brand-mark">KRTV</div>
    <address class="company-contact">
      <div class="company-name">K.R. Thorne and Venture PLLC</div>
      <div class="contact-line">
        <svg width="18" height="18" viewBox="0 0 18 18"><circle cx="9" cy="9" r="9" fill="#fff"/><path d="M6 4.5l2 2-1 1.3c.6 1.3 1.6 2.3 2.9 2.9l1.3-1 2 2-1.2 1.6C9 13 5 9 4.5 5.7z" fill="var(--brand-blue)"/></svg>
        <span>555-014-2786</span>
      </div>
      <div class="contact-line">
        <svg width="18" height="18" viewBox="0 0 18 18"><circle cx="9" cy="9" r="9" fill="#fff"/><circle cx="9" cy="9" r="5" fill="none" stroke="var(--brand-blue)" stroke-width="1.5"/><path d="M4 9h10M9 4c-2 3-2 7 0 10M9 4c2 3 2 7 0 10" stroke="var(--brand-blue)" stroke-width="1" fill="none"/></svg>
        <span>www.krtvtech.example</span>
      </div>
      <div class="contact-line">
        <svg width="18" height="18" viewBox="0 0 18 18"><circle cx="9" cy="9" r="9" fill="#fff"/><path d="M9 3.5a3.5 3.5 0 0 1 3.5 3.5c0 2.5-3.5 7-3.5 7S5.5 9.5 5.5 7A3.5 3.5 0 0 1 9 3.5z" fill="var(--brand-blue)"/><circle cx="9" cy="7" r="1.3" fill="#fff"/></svg>
        <span>48 W. Alder Ave, Bldg. 2 Pine Hollow,<br>Arizona 86099, USA</span>
      </div>
    </address>
    <nav class="main-nav">
      <a href="#">PRODUCTS</a>
      <a href="#">SERVICES</a>
      <a href="#">ABOUT US</a>
      <a href="#">CONTACT US</a>
    </nav>
    <h1 class="hero-title">HIGH TEMPERATURE<br>INSULATIONS</h1>
    <div class="slider-controls">
      <span class="slider-arrow"><svg width="8" height="10" viewBox="0 0 8 10"><path d="M6 1L2 5l4 4" stroke="var(--brand-blue)" stroke-width="1.6" fill="none"/></svg></span>
      <span class="slider-dots"><span class="slider-dot is-active"></span><span class="slider-dot"></span><span class="slider-dot"></span><span class="slider-dot"></span></span>
      <span class="slider-arrow"><svg width="8" height="10" viewBox="0 0 8 10"><path d="M2 1l4 4-4 4" stroke="var(--brand-blue)" stroke-width="1.6" fill="none"/></svg></span>
    </div>
  </section>

  <footer>
    <div class="footer-brand"><span class="brand-dot"></span><span>KRTV</span></div>
    <div class="footer-col col-info">
      <h3>INFORMATION</h3>
      <ul><li>About Us</li><li>Careers</li><li>Privacy &amp; Security</li><li>Site Map</li><li>Terms of Use</li><li>Blog</li></ul>
    </div>
    <div class="footer-col col-help">
      <h3>HELP &amp; SUPPORT</h3>
      <ul><li>Recommended Reading</li><li>Submit your Story</li><li>Contact Us</li><li>Frequently Asked Questions</li><li>How to Order</li></ul>
    </div>
    <div class="footer-col col-account">
      <h3>MY ACCOUNT</h3>
      <ul><li>Delivery Information</li><li>My Account</li><li>Order Tracking</li><li>Reminder Service</li><li>Shipping, Returns &amp; Fees</li></ul>
    </div>
    <div class="footer-rule"></div>
    <p class="copyright">Copyright © 2018, KRTV. All Rights Reserved.</p>
    <div class="social-links">
      <a href="#" aria-label="Share">
        <svg width="16" height="16" viewBox="0 0 16 16"><circle cx="12" cy="3.5" r="2" fill="var(--social-ink)"/><circle cx="4" cy="8" r="2" fill="var(--social-ink)"/><circle cx="12" cy="12.5" r="2" fill="var(--social-ink)"/><path d="M12 3.5L4 8l8 4.5" stroke="var(--social-ink)" stroke-width="1.4" fill="none"/></svg>
      </a>
      <a href="#" aria-label="Message">
        <svg width="16" height="16" viewBox="0 0 16 16"><path d="M2 3h12v8H7l-3 3v-3H2z" fill="var(--social-ink)"/></svg>
      </a>
      <a href="#" aria-label="Email">
        <svg width="16" height="16" viewBox="0 0 16 16"><rect x="1.5" y="3.5" width="13" height="9" rx="1" fill="none" stroke="var(--social-ink)" stroke-width="1.5"/><path d="M2 4l6 5 6-5" stroke="var(--social-ink)" stroke-width="1.5" fill="none"/></svg>
      </a>
      <a href="#" aria-label="Link">
        <svg width="16" height="16" viewBox="0 0 16 16"><path d="M7 9l2-2M6 6.5L4.5 8a2.5 2.5 0 0 0 3.5 3.5L9.5 10M10 9.5L11.5 8A2.5 2.5 0 0 0 8 4.5L6.5 6" stroke="var(--social-ink)" stroke-width="1.6" fill="none" stroke-linecap="round"/></svg>
      </a>
    </div>
  </footer>
</body>
</html>
```